Luxury WordPress Website for CORALBASINS

I need a professional WordPress website for Coral Basins. The site should be modern, visually appealing, and user-friendly, reflecting the brand’s luxury and premium identity. It must include a homepage, product/service pages, contact form, and be responsive on both desktop and mobile devices. The design should allow for easy updates and integration of future content, while maintaining a polished and professional look.

Target Market(s)

swimmingpool & spa

Industry/Entity Type

Swimmingpool

Coding

Coded - Design and coding required

Font styles to use
Other font styles liked:
• HaboroSoft

Requirements
Must have
• Exclusive appearance
Nice to have
• • A logo that subtly incorporates water or pool elements. • A color palette that reflects luxury, elegance, and relaxation. • Clean and modern typography that is easy to read across all media. • Iconography or design elements that convey premium quality. • A versatile design that can be adapted for social media, merchandise, and promotional materials. • Optional: A tagline that emphasizes luxury and high-end pool experiences.

```html
<!DOCTYPE html>
<html lang="en">
<head>
<meta charset="utf-8">
<title>Coral Basins — Luxury Pools</title>
<link href="https://fonts.googleapis.com/css2?family=Inter:wght@400;500;600;700;800&display=swap" rel="stylesheet">
<style>
:root{
  --accent:#9a8af0;
  --accent-head:#9787ea;
  --band:#9686ef;
  --ink:#1d1d22;
  --muted:#7c8694;
  --card-line:#8d9be0;
  --header-bg:#e5e5e7;
  --white:#ffffff;
}
*{box-sizing:border-box;margin:0;padding:0}
html,body{width:1200px;height:4326px;overflow:hidden}
body{font-family:"Inter",sans-serif;color:var(--ink);background:var(--white);position:relative}
.abs{position:absolute}

/* header */
.site-header{left:0;top:0;width:1200px;height:116px;background:var(--header-bg)}
.brand{left:100px;top:44px;font-size:20px;font-weight:600;color:var(--accent);letter-spacing:1px}
.nav{left:569px;top:46px;display:flex;gap:24px;font-size:17px}
.btn-consult{left:965px;top:32px;width:151px;height:50px;border-radius:25px;background:var(--accent);color:#fff;font-size:17px;display:flex;align-items:center;justify-content:center}

/* hero */
.hero{left:0;top:116px;width:1200px;height:532px;background:linear-gradient(180deg,#4c4a49 0%,#3d4547 45%,#2f5158 80%,#355e66 100%)}
.hero-badge{left:424px;top:222px;width:352px;height:25px;border-radius:13px;background:rgba(255,255,255,.18);color:#fff;font-size:11px;display:flex;align-items:center;justify-content:center}
.hero-title{left:0;top:275px;width:1200px;text-align:center;color:#fff;font-size:54px;font-weight:600;letter-spacing:7px;line-height:58px}
.hero-sub{left:300px;top:420px;width:600px;text-align:center;color:#fff;font-size:17px;line-height:25px}
.btn-explore{left:498px;top:497px;width:203px;height:52px;border-radius:26px;background:var(--accent);color:#fff;font-size:17px;display:flex;align-items:center;justify-content:center}

/* about */
.about-frame{left:84px;top:732px;width:310px;height:340px;border:3px solid var(--ink);border-right:none;border-radius:30px 30px 0 60px}
.about-photo{left:101px;top:746px;width:357px;height:360px;border-radius:30px 30px 30px 60px;background:linear-gradient(180deg,#9fb5c6 0%,#c0b6a4 40%,#2f8fd6 62%,#1a78d8 100%)}
.about-title{left:534px;top:770px;font-size:36px;font-weight:700;color:var(--accent-head)}
.about-text{left:534px;top:838px;width:580px;font-size:20px;line-height:30px}
.btn-outline{left:534px;top:1013px;width:139px;height:51px;border-radius:26px;border:1.5px solid var(--accent);color:var(--accent);font-size:16px;display:flex;align-items:center;justify-content:center}

/* section heads */
.sec-title{left:84px;font-size:46px;font-weight:700;color:var(--accent-head);line-height:50px}
.sec-lede{right:84px;text-align:right;font-size:20px;line-height:22px}

/* cards */
.card{width:317px;border:1.5px solid var(--card-line);border-radius:14px;background:#fff}
.card-photo{position:absolute;left:11px;top:15px;width:293px;height:212px;border-radius:12px}
.card h3{position:absolute;left:12px;top:262px;font-size:20px;font-weight:600}
.card p{position:absolute;left:12px;top:302px;width:282px;font-size:16.5px;line-height:25px;color:var(--muted)}

/* contact */
.contact-band{left:0;top:2361px;width:1200px;height:740px;background:var(--band)}
.contact-title{left:0;top:2440px;width:1200px;text-align:center;color:#fff;font-size:44px;font-weight:700}
.contact-sub{left:0;top:2512px;width:1200px;text-align:center;color:#fff;font-size:20px}
.field{border:1.5px solid rgba(255,255,255,.8);border-radius:6px;background:rgba(255,255,255,.12);color:#fff;font-size:19px;font-weight:600;padding:22px 24px}
.btn-send{left:84px;top:2948px;width:1032px;height:71px;border-radius:6px;background:#fff;font-size:19px;font-weight:500;display:flex;align-items:center;justify-content:center}

/* blog */
.post{width:317px;height:452px;border:1.5px solid var(--card-line);border-radius:14px;background:#fff;text-align:left}
.post-photo{position:absolute;left:11px;top:15px;width:293px;height:213px;border-radius:12px;border:5px solid #e2e2ea}
.post h3{position:absolute;left:12px;top:262px;width:295px;font-size:20px;font-weight:600;line-height:22px}
.post p{position:absolute;left:12px;width:295px;font-size:16.5px;line-height:25px;color:var(--muted)}
.post .more{position:absolute;left:0;width:317px;display:flex;justify-content:center;align-items:center;gap:12px;color:#3a3fa0;font-size:16.5px}

/* footer */
.foot-brand{left:100px;top:4044px;font-size:20px;font-weight:600;color:var(--accent);letter-spacing:1px}
.foot-about{left:84px;top:4117px;width:320px;font-size:16.5px;line-height:25px}
.foot-col{font-size:16.5px;line-height:33px}
.foot-col h4{font-size:16.5px;font-weight:700;margin-bottom:4px}
.social{display:flex;align-items:center;gap:12px;padding-left:6px}
.social i{display:inline-block;width:10px;height:10px;border:1.5px solid var(--ink);border-radius:2px}
.foot-rule{left:84px;top:4242px;width:1032px;height:1px;background:#d8d8dc}
.foot-bottom{top:4256px;font-size:16.5px}
</style>
</head>
<body>

<header class="abs site-header"></header>
<div class="abs brand">CORALBASINS</div>
<nav class="abs nav"><span>Home</span><span>About</span><span>Product/Services</span><span>Contact</span></nav>
<div class="abs btn-consult">Consultation</div>

<section class="abs hero" role="img" aria-label="Luxury villa poolside terrace with lounge furniture at dusk"></section>
<div class="abs hero-badge">B2B DISTRIBUTOR DESIGNEER BUILDERS CONTRACTORS</div>
<h1 class="abs hero-title">EXPERIENCE THE ART OF<br>LUXURY POOLS</h1>
<p class="abs hero-sub">Crafted for elegance, durability, and timeless beauty — Coral Basins brings your dream oasis to life.</p>
<div class="abs btn-explore">Explore Collections</div>

<div class="abs about-frame"></div>
<div class="abs about-photo" role="img" aria-label="Resort hotel with large blue swimming pool"></div>
<h2 class="abs about-title">About Coral Basins</h2>
<p class="abs about-text">Coral Basins is dedicated to designing and constructing exclusive pools for those who seek the finest craftsmanship and sophistication. Our pools combine premium materials, advanced technology, and aesthetic perfection to create spaces that inspire relaxation and elevate your lifestyle.</p>
<div class="abs btn-outline">Learn More</div>

<h2 class="abs sec-title" style="top:1272px">Our Expertise</h2>
<p class="abs sec-lede" style="top:1265px;width:640px">From concept to completion, Coral Basins delivers unmatched quality, innovation, and beauty — redefining what it means to own a luxury pool.</p>

<article class="abs card" style="left:84px;top:1351px;height:441px">
  <div class="card-photo" role="img" aria-label="Garden pool with trees and parasol" style="background:linear-gradient(180deg,#c9a24e 0%,#6f8a3a 45%,#2fb3b8 70%,#1c9fb0 100%)"></div>
  <h3>Luxury Pool Design</h3>
  <p>We create timeless, tailor-made pool designs that harmonize with your architecture and lifestyle — blending elegance, innovation, and comfort.</p>
</article>
<article class="abs card" style="left:441px;top:1351px;height:441px">
  <div class="card-photo" role="img" aria-label="White modern house with backyard pool" style="background:linear-gradient(180deg,#8a9a6a 0%,#d6d6d2 40%,#7fc4da 70%,#4aa8cf 100%)"></div>
  <h3>Custom Pool Construction</h3>
  <p>Built with precision and premium materials, our pools are engineered for durability and long-term performance without compromising beauty.</p>
</article>
<article class="abs card" style="left:799px;top:1351px;height:441px">
  <div class="card-photo" role="img" aria-label="Spa storage and wellness equipment room" style="background:linear-gradient(90deg,#8d8f92 0%,#d9d7d2 40%,#b8a58a 70%,#8a8c8f 100%)"></div>
  <h3>Spa &amp; Wellness Integration</h3>
  <p>Experience complete tranquility with integrated spa features — from hydrotherapy jets to heated relaxation zones that turn your pool into a private sanctuary.</p>
</article>

<article class="abs card" style="left:84px;top:1836px;height:441px">
  <div class="card-photo" role="img" aria-label="Indoor pool with smartphone control app" style="background:linear-gradient(180deg,#c7d3dc 0%,#8fb7d0 45%,#3a9ad0 100%)"></div>
  <h3>Smart Pool Technology</h3>
  <p>Our pools feature cutting-edge automation systems — intelligent water management, lighting, and temperature control all at your fingertips.</p>
</article>
<article class="abs card" style="left:441px;top:1836px;height:441px">
  <div class="card-photo" role="img" aria-label="Renovated white house with garden" style="background:linear-gradient(180deg,#e8b9b8 0%,#e0dcd8 40%,#7f8f6c 80%,#5c6a4c 100%)"></div>
  <h3>Renovation &amp; Modernization</h3>
  <p>Transform existing pools into modern masterpieces. We restore, upgrade, and redesign to match contemporary aesthetics and sustainability standards.</p>
</article>
<article class="abs card" style="left:799px;top:1836px;height:441px">
  <div class="card-photo" role="img" aria-label="Modern villa pool lit at night" style="background:linear-gradient(180deg,#3e5fa8 0%,#8c8c8c 40%,#1e6ad8 70%,#0e47b8 100%)"></div>
  <h3>Maintenance &amp; After-Care</h3>
  <p>Our expert team ensures your pool stays pristine year-round with scheduled cleaning, water balancing, and technical inspections.</p>
</article>

<section class="abs contact-band"></section>
<h2 class="abs contact-title">Get In Touch</h2>
<p class="abs contact-sub">We’re ready to bring your vision to life. Contact us to start building your exclusive pool today.</p>
<div class="abs field" style="left:84px;top:2561px;width:503px;height:72px">Contact Name</div>
<div class="abs field" style="left:612px;top:2561px;width:504px;height:72px">Company</div>
<div class="abs field" style="left:84px;top:2658px;width:503px;height:72px">Email</div>
<div class="abs field" style="left:612px;top:2658px;width:504px;height:72px">Phone</div>
<div class="abs field" style="left:84px;top:2755px;width:1032px;height:166px">Tell us about your project</div>
<div class="abs btn-send">Send Message</div>

<h2 class="abs sec-title" style="top:3188px">Insights &amp;<br>Inspiration</h2>
<p class="abs sec-lede" style="top:3225px;width:640px">Expert tips, design trends, and stories behind exceptional pools.</p>

<article class="abs post" style="left:84px;top:3338px">
  <div class="post-photo" role="img" aria-label="Infinity pool with pavilion overlooking hills" style="background:linear-gradient(180deg,#b9c3c4 0%,#8b8f78 50%,#2fb1b9 75%,#1a98a8 100%)"></div>
  <h3>Designing the Perfect Infinity Pool for Modern Homes</h3>
  <p style="top:323px;text-align:center">Discover the essential principles for creating seamless infinity edges, optimal viewpoints, and flawless</p>
  <div class="more" style="top:411px">Read More <svg width="20" height="12" viewBox="0 0 20 12"><path d="M1 6h17M13 1l5 5-5 5" fill="none" stroke="#3a3fa0" stroke-width="1.8"/></svg></div>
</article>
<article class="abs post" style="left:441px;top:3338px">
  <div class="post-photo" role="img" aria-label="Modern house pool with smartphone app control" style="background:linear-gradient(180deg,#cfd6dc 0%,#9aa2a6 50%,#5aa8c8 100%)"></div>
  <h3>Smart Pool Technology: Automation That Elevates Luxury</h3>
  <p style="top:345px;text-align:center">Automation redefines convenience — from automated filtration and ...</p>
  <div class="more" style="top:408px">Read More <svg width="20" height="12" viewBox="0 0 20 12"><path d="M1 6h17M13 1l5 5-5 5" fill="none" stroke="#3a3fa0" stroke-width="1.8"/></svg></div>
</article>
<article class="abs post" style="left:799px;top:3338px">
  <div class="post-photo" role="img" aria-label="Mediterranean mansion with curved pool" style="background:linear-gradient(180deg,#a9c4dc 0%,#8d7e68 50%,#42c0c8 80%,#2aa7b5 100%)"></div>
  <h3>Materials That Matter: Tiles, Edges, and Finishes</h3>
  <p style="top:323px;text-align:center">Choosing premium materials defines both the longevity and luxury of your pool.</p>
  <div class="more" style="top:411px">Read More <svg width="20" height="12" viewBox="0 0 20 12"><path d="M1 6h17M13 1l5 5-5 5" fill="none" stroke="#3a3fa0" stroke-width="1.8"/></svg></div>
</article>

<footer>
  <div class="abs foot-brand">CORALBASINS</div>
  <p class="abs foot-about">Exclusive pools crafted for those who seek the finest in design, durability, and luxury.</p>
  <div class="abs foot-col" style="left:508px;top:4022px"><h4>Quick Links</h4>Home<br>About<br>Products<br>Contact</div>
  <div class="abs foot-col" style="left:661px;top:4022px"><h4>Company</h4>Email : contact@coralbasins.com<br>Phone: +1 (555) 014-2290</div>
  <div class="abs foot-col" style="left:1003px;top:4022px"><h4>Connect</h4>
    <div class="social"><i></i>Ripplebook</div>
    <div class="social"><i></i>Lumenshare</div>
    <div class="social"><i></i>Workline</div>
  </div>
  <div class="abs foot-rule"></div>
  <div class="abs foot-bottom" style="left:84px">Privacy and Policy</div>
  <div class="abs foot-bottom" style="right:84px">© 2025 Coral Basins. All rights reserved.</div>
</footer>

</body>
</html>
```